Brindle Sky Port needs a new upscale business card design for our high end aircraft hangar complex

Brindle Sky Port (BSP) is a large, upscale jet hangar complex in the US housing expensive aircraft. We need a new business card design, using our current logo. We will be attending a industry convention and need a card design that will stand out and be remembered by aircraft owners and private pilots.

Target Market(s)

Aircraft pilots or owners looking for a new upscale hangar

Industry/Entity Type

Airport

Contact Information for Business Card

I like to use very heavy card stock, 400#, double sided. Square, no rounded edges please.

Colors
3276b5
0255a3
85abd2

Requirements
Must have
• An expensive, classy design, vivid colors.
Nice to have
• Needs to look very expensive and classy, and have some "pop". Designer must be able to download or copy my current typeface or fonts.
• One card side might be black with the "Logo and Brindle Sky Port Double line image in blue (or try gold, or glossy black), and perhaps have a grayed out "K720 jet silhouette". The other card side would have our contact info, and perhaps the "BSP Logo only". I'd like my contact info 'stacked', not in a paragraph format.
Should not have
• Should not look "too busy". Having a double-sided card will help.

```html
<!DOCTYPE html>
<html lang="en">
<head>
<meta charset="utf-8">
<title>Brindle Sky Port – Business Card</title>
<link href="https://fonts.googleapis.com/css2?family=Exo+2:wght@600;700&family=Source+Sans+3:wght@400&display=swap" rel="stylesheet">
<style>
  :root {
    --backdrop: #8e8e8e;
    --card: #0f0f11;
    --card-edge: #1a1a1d;
    --brand-blue: #2f69a8;
    --brand-deep: #0255a3;
    --brand-light: #85abd2;
    --text-light: #d9d9d9;
    --rule: #6a6a6a;
    --silhouette: #262628;
  }
  * { margin: 0; padding: 0; box-sizing: border-box; }
  html, body {
    width: 1105px; height: 1200px; overflow: hidden;
    background: var(--backdrop);
  }
  .card {
    position: absolute; left: 172px;
    width: 760px; height: 436px;
    background: var(--card);
    overflow: hidden;
  }
  .card--front { top: 120px; }
  .card--back { top: 644px; }

  /* Front */
  .brand-mark {
    position: absolute; right: 42px; top: 38px;
    font-family: "Exo 2", sans-serif; font-weight: 700;
    font-size: 96px; letter-spacing: 4px; line-height: 1;
    color: var(--brand-blue);
  }
  .person-name {
    position: absolute; left: 40px; top: 176px;
    font-family: "Exo 2", sans-serif; font-weight: 600;
    font-size: 27px; color: var(--brand-blue);
  }
  .person-title {
    position: absolute; left: 40px; top: 214px;
    font-family: "Source Sans 3", sans-serif;
    font-size: 20px; color: var(--text-light);
  }
  .divider {
    position: absolute; left: 40px; right: 42px; top: 264px;
    height: 1px; background: var(--rule);
  }
  .contact-list {
    position: absolute; left: 40px; top: 281px;
    list-style: none;
    font-family: "Source Sans 3", sans-serif;
    font-size: 20px; line-height: 28.5px; color: var(--text-light);
  }
  .contact-list .label {
    display: inline-block; width: 22px;
    color: var(--brand-blue);
  }
  .address {
    position: absolute; right: 42px; top: 310px;
    text-align: right; font-style: normal;
    font-family: "Source Sans 3", sans-serif;
    font-size: 20px; line-height: 28.5px; color: var(--text-light);
  }
  .address .web { letter-spacing: 4.5px; }
  .edge-band {
    position: absolute; left: 0; right: 0; bottom: 0; height: 17px;
    border-top: 2px solid var(--rule);
    background: linear-gradient(180deg, var(--brand-blue), var(--brand-deep) 60%, #0a3a73);
  }

  /* Back */
  .jet-silhouette {
    position: absolute; left: 0; top: 0; width: 760px; height: 436px;
    background:
      radial-gradient(ellipse 170px 200px at 160px 320px, var(--silhouette), transparent 75%),
      linear-gradient(180deg, transparent 88%, #1c1c1e 92%, transparent 96%);
  }
  .brand-lockup {
    position: absolute; left: 398px; top: 82px; width: 310px;
    text-align: center;
    font-family: "Exo 2", sans-serif; font-weight: 700;
    color: var(--brand-blue); text-transform: uppercase;
  }
  .brand-lockup .initials {
    display: block; font-size: 136px; line-height: 1; letter-spacing: 6px;
  }
  .brand-lockup .full-name {
    display: block; font-size: 36px; line-height: 1.05; letter-spacing: 3px;
    margin-top: 6px;
  }
</style>
</head>
<body>
  <section class="card card--front" aria-label="Business card front">
    <div class="brand-mark">BSP</div>
    <h1 class="person-name">Evan Hollis</h1>
    <p class="person-title">CEO/Founder</p>
    <div class="divider"></div>
    <ul class="contact-list">
      <li><span class="label">P</span>(612) 408-7731</li>
      <li><span class="label">C</span>(612) 555-2190</li>
      <li><span class="label">F</span>(612) 408-7735</li>
      <li><span class="label">E</span>hello@brindlesky.com</li>
    </ul>
    <address class="address">
      2140 Larkspur Way<br>
      Fairbanks, Alaska 99701<br>
      <span class="web">www.brindlesky.com</span>
    </address>
    <div class="edge-band"></div>
  </section>

  <section class="card card--back" aria-label="Business card back">
    <div class="jet-silhouette" role="img" aria-label="Faded dark grey private jet seen head-on"></div>
    <div class="brand-lockup">
      <span class="initials">BSP</span>
      <span class="full-name">Brindle<br>Sky Port</span>
    </div>
  </section>
</body>
</html>
```